Website Re-Design and Refresh

We are looking for a redesign of www.brightmeadow-example.com the deliverable is a graphic which will be used as a template for the main site.
The Logo will remain the same
The Video currently shown must be included in your submission
Search Element must be included, this should be better visible than it is currently
All navigation current on the left is to be moved to the right.
Top left column should be a “Quick Quotation” element. It should stand out and draw the eye as that is the conversion that we aim for on our site. This is the purpose of the site to attract these.
Add Testimonials navigation that users can click upon.
Below this element on the right “Recent Posts” should become Latest News”
We want users to see how much press coverage the site has had, the following UK’s news logos should be used Courier, Morning Ledger, NVR and The Wayfarer.
Please use the current text from our site but make some main features which we want to draw attention to. 5 points and use fake text, using a bullet point, icon, graphic or colour to make it stick out the most.
Large Guarantee, shown through a Seal graphic. An example of this type of style is attached.
Updates

Please note that as per the brief we want to havenews/contact forms down the left hand side of the page. This is to comply with “F”shapeeye pattern which shows that users look mostly on the left of webpages.

Please make the quick quotes more distinctive and use of thefields suggested in the brief.

As you appear to like using vivid colours, please see thefollowing examples we like of vivid colours.

 

http://media.tallcrane-example.com/cpw-sales/static/images/common/global_nav/nnp_03.png

http://media.tallcrane-example.com/cpw-sales/static/sections/homepage/2012_04/images/ban_big_promises.png

http://media.tallcrane-example.com/cpw-sales/static/images/landing_pages/mobile_phones/April_2012/mp_hero2_v3.jpg

http://media.tallcrane-example.com/cpw-sales/static/sections/upgrades/images/sidebanner_payg_upgrades.gif

Pleaseamend your designs so that they adhere to the following:

 

Thereis a quick quotation form, as per brief, next to the video positionedon the left, the video on the right so they are the first items the userssee. 

 

The"seal" guarantee should be top right and 

Newsand Testimonials should be on the right hand side

 

Inthe main content text area please use latin ipsom lorem text and put 5 bulletpoints in large writing and latin below. Such as:

 

Lorem Ipsum 

Lorem Ipsum 

Lorem Ipsum 

Lorem Ipsum 

Lorem Ipsum 

 

Lorem Ipsum is simply dummy text ofthe printing and typesetting industry. Lorem Ipsum has been the industry'sstandard dummy text ever since the 1500s, when an unknown printer took a galleyof type and scrambled it to make a type specimen book. It has survived not onlyfive centuries, but also the leap into electronic typesetting, remainingessentially unchanged. It was popularised in the 1960s with the release ofLetraset sheets containing Lorem Ipsum passages, and more recently with desktoppublishing software like Quorin SheetSmith including versions of Lorem Ipsum.

The following design is a good indication of style and the use of bright colors. Although the positioning of some elements is not as per the brief. 

Please see best deigns so far:

Target Market(s)

Business To Business

Industry/Entity Type

News

Requirements
Must have
• The Logo will remain the same
Top right should be a “Quick Quotation” element. It should stand out and draw the eye as that is the conversion that we aim for on our site. This is the purpose of the site to attract these.

```html
<!DOCTYPE html>
<html lang="en">
<head>
<meta charset="utf-8">
<title>Brightmeadow – Reputation Management</title>
<link href="https://fonts.googleapis.com/css2?family=Arimo:ital,wght@0,400;0,700;1,700&family=PT+Sans:wght@400;700&display=swap" rel="stylesheet">
<style>
:root{
  --green:#3f8c0a;
  --green-dark:#2f7606;
  --green-btn:#3aa012;
  --text:#444;
  --bar:#333;
  --footer:#3a3a3a;
  --band:#eef1e6;
  --hero:#f4f7ee;
  --white:#fff;
}
*{box-sizing:border-box;margin:0;padding:0}
html,body{width:988px;height:1200px;overflow:hidden}
body{position:relative;background:var(--white);font-family:Arimo,Arial,sans-serif;color:var(--text);font-size:10px;line-height:1.45}
.abs{position:absolute}
strong.hl{color:var(--green);font-weight:700}

/* header */
.site-header{top:0;left:0;width:988px;height:101px;background:linear-gradient(#fff,#f7f9f4)}
.brand{left:99px;top:34px;display:flex;align-items:center;gap:10px;font:700 34px "PT Sans",sans-serif;color:var(--green);letter-spacing:-.5px}
.brand-mark{width:26px;height:26px;background:var(--green);border-radius:50%}
.quote-btn{left:747px;top:21px;width:149px;height:58px;border-radius:4px;background:linear-gradient(#4fb51b,#2f8f08);box-shadow:0 2px 4px rgba(0,0,0,.25);color:#fff;font:700 17px "PT Sans",sans-serif;text-align:center;padding-top:9px;letter-spacing:-.3px}
.quote-btn .bubble{display:block;margin:0 auto 1px;width:26px;height:16px;border-radius:8px;background:#fff}

/* nav */
.nav-bar{top:101px;left:0;width:988px;height:41px;background:var(--bar)}
.search{left:91px;top:10px;display:flex;gap:8px}
.search-field{width:144px;height:19px;background:#fff;border-radius:3px}
.search-btn{width:20px;height:20px;background:#5fb52a;border-radius:2px;display:flex;align-items:center;justify-content:center}
.main-nav{right:91px;top:14px;display:flex;gap:14px;font-size:9.4px;color:#fff;text-transform:uppercase;letter-spacing:.1px}

/* hero */
.hero{top:142px;left:0;width:988px;height:286px;background:linear-gradient(90deg,#f1f5ea,#fbfcf8)}
.hero-copy{left:104px;top:66px;width:322px;z-index:2}
.hero-copy h1{font:italic 700 21px/22px Arimo,sans-serif;color:var(--green);margin-bottom:13px;white-space:nowrap}
.hero-copy p{font-size:10.2px;line-height:12.7px;margin-bottom:13px}
.btn{display:inline-block;background:linear-gradient(#46ad16,#2f8c08);color:#fff;font-size:8px;font-weight:700;padding:4px 6px;border-radius:2px;box-shadow:0 1px 2px rgba(0,0,0,.3)}
.screen{left:445px;top:13px;width:414px;height:250px;background:#111;border-radius:6px 6px 0 0;padding:16px 13px 12px}
.screen-inner{width:100%;height:100%;background:linear-gradient(#eef3f7,#f8fafc 70%,#e9eef1)}
.video-play{left:170px;top:74px}
.laptop-base{left:407px;top:263px;width:490px;height:18px;border-radius:0 0 10px 10px;background:linear-gradient(#e8e8e8,#b9b9b9);box-shadow:0 3px 4px rgba(0,0,0,.15)}
.slider-dots{left:208px;top:5px;display:flex;gap:8px}
.slider-dots span{width:8px;height:8px;border-radius:50%;border:1px solid #999;background:#fff}
.slider-dots span.on{background:#222;border-color:#222}

/* features */
.features{top:428px;left:0;width:988px;height:177px;background:var(--white)}
.feature{top:34px;width:182px}
.feature-head{display:flex;align-items:center;gap:9px;border-bottom:3px solid var(--green);padding-bottom:5px;height:43px}
.feature-icon{width:32px;height:32px;border-radius:6px;background:linear-gradient(#cfe0ef,#7fa6c8);flex:none}
.feature-head h2{font:400 17px/16.5px "PT Sans",sans-serif;color:var(--green)}
.feature ul{list-style:none;margin-top:7px}
.feature li{position:relative;padding-left:17px;height:18px;font-size:9.6px}
.feature li::before{content:"";position:absolute;left:6px;top:5px;width:4px;height:4px;border-radius:50%;background:#333}
.feature p{margin-top:7px;font-size:9.6px;line-height:14.8px}

/* content band */
.band{top:605px;left:0;width:988px;height:321px;background:var(--band)}
.panel{left:91px;top:38px;width:806px;height:236px;background:#fff;border:1px solid #e2e6da;box-shadow:0 3px 4px rgba(0,0,0,.08)}
.panel-divider{left:534px;top:0;width:1px;height:236px;background:#e3e3e3}
.section-title{background:var(--green);color:#fff;font:400 16px/29px "PT Sans",sans-serif;padding-left:8px;height:29px;box-shadow:0 3px 3px rgba(0,0,0,.15)}
.about{left:14px;top:11px;width:505px}
.about p{font-size:9.4px;line-height:12px;text-align:justify;margin-top:15px}
.about p:first-of-type{margin-top:20px}
.about .btn{margin-top:13px}
.news{left:549px;top:11px;width:242px}
.news-item{margin-top:19px;font-size:9.4px;line-height:12px;text-align:justify}
.news-item + .news-item{margin-top:25px}
.news-thumb{float:left;width:32px;height:30px;margin:0 7px 2px 0;background:linear-gradient(#6d6258,#2d2622)}
.news-date{display:block;font-style:italic;font-weight:700;color:var(--green)}
.news .btn{margin-top:14px}

/* press */
.press{top:926px;left:0;width:988px;height:92px;background:#fff}
.press-list{left:91px;top:30px;width:806px;display:flex;justify-content:space-between;align-items:center}
.press-name{font:700 19px "PT Sans",sans-serif;color:#111;letter-spacing:-.3px}
.press-name.boxed{display:flex;align-items:center;gap:6px}
.press-name.boxed i{width:20px;height:20px;background:#111}

/* footer */
.site-footer{top:1018px;left:0;width:988px;height:182px;background:var(--footer);color:#fff}
.footer-col{top:23px;list-style:none;font-size:10.2px;line-height:16.5px}
.footer-rule{left:91px;top:110px;width:607px;height:1px;background:#5a5a5a}
.copyright{left:103px;top:118px;width:595px;font-size:9.8px;line-height:12px}
.social{left:103px;top:155px;display:flex;gap:8px}
.social span{width:16px;height:16px;border-radius:2px;background:#8aa4c4}
.social span:first-child{background:#e8892a}
.social span:last-child{background:#e05a3a}
.seal{left:695px;top:21px;width:198px;height:146px;border-radius:50%;background:radial-gradient(circle at 50% 45%,#f7d56a,#e2a51d 55%,#c4401f 80%,transparent 81%)}
</style>
</head>
<body>

<header class="site-header abs">
  <div class="brand abs"><span class="brand-mark"></span>brightmeadow</div>
  <a class="quote-btn abs"><span class="bubble"></span>Quick Quotation</a>
</header>

<nav class="nav-bar abs">
  <div class="search abs">
    <div class="search-field"></div>
    <div class="search-btn">
      <svg width="12" height="12" viewBox="0 0 12 12"><circle cx="5" cy="5" r="3.5" fill="none" stroke="#1d3a0a" stroke-width="1.6"/><path d="M7.5 7.5 11 11" stroke="#1d3a0a" stroke-width="1.8"/></svg>
    </div>
  </div>
  <div class="main-nav abs">
    <span>Reputation Management</span>
    <span>Online Reputation Management – ORM</span>
    <span>Brand Protection</span>
    <span>Prices</span>
    <span>Testimonials</span>
  </div>
</nav>

<section class="hero abs">
  <div class="hero-copy abs">
    <h1>Place Your Business at the<br>top of Search Engines</h1>
    <p>Lorem Ipsum is simply dummy text of the printing and typesetting industry. Lorem Ipsum has been the industry's standard dummy text ever since the 1500s.</p>
    <p>When an unknown printer took a galley of type and scrambled it to make a type specimen book.</p>
    <a class="btn">Read More</a>
  </div>
  <div class="screen abs">
    <div class="screen-inner" role="img" aria-label="Video showing how a website spreads across search engines and social sites"></div>
    <svg class="video-play abs" width="74" height="74" viewBox="0 0 74 74"><circle cx="37" cy="37" r="37" fill="#111"/><path d="M29 21 55 37 29 53Z" fill="#fff"/></svg>
  </div>
  <div class="laptop-base abs">
    <div class="slider-dots abs"><span></span><span class="on"></span><span></span><span></span><span></span></div>
  </div>
</section>

<section class="features abs">
  <div class="feature abs" style="left:91px">
    <div class="feature-head"><div class="feature-icon" role="img" aria-label="Certificate icon"></div><h2>Reputation<br>Management</h2></div>
    <ul>
      <li><strong class="hl">Lorem Ipsum</strong> is simply dummy text</li>
      <li>Of the printing and <strong class="hl">typesetting</strong></li>
      <li>Lorem Ipsum has been the <strong class="hl">industry's</strong></li>
      <li>Standard <strong class="hl">dummy</strong> text ever</li>
    </ul>
  </div>
  <div class="feature abs" style="left:300px">
    <div class="feature-head"><div class="feature-icon" role="img" aria-label="Globe with quill icon"></div><h2>Online Reputation<br>Management</h2></div>
    <p>Praesent accumsan <strong class="hl">bibendum</strong> risus fringilla <strong class="hl">tincidunt</strong>. Cum sociis natoque penatibus et magnis dis <strong class="hl">parturient montes</strong>, nascetur ridiculus musnec sollicitudin vulputate felis.</p>
  </div>
  <div class="feature abs" style="left:507px">
    <div class="feature-head"><div class="feature-icon" role="img" aria-label="Document with globe icon"></div><h2>Online<br>Reputation</h2></div>
    <ul>
      <li><strong class="hl">Lorem Ipsum</strong> is simply dummy text</li>
      <li>Of the printing and <strong class="hl">typesetting</strong></li>
      <li>Lorem Ipsum has been the <strong class="hl">industry's</strong></li>
      <li>Standard <strong class="hl">dummy</strong> text ever</li>
    </ul>
  </div>
  <div class="feature abs" style="left:717px">
    <div class="feature-head"><div class="feature-icon" role="img" aria-label="Shield icon"></div><h2>Brand<br>Protection</h2></div>
    <p>Donec <strong class="hl">ornare</strong> turpis in nisi condimentum a accumsan massa auctor. <strong class="hl">Quisque viverra rhoncus</strong> nisl at euismod. Vivamus luctus cursus ultricies. Ut porttitor <strong class="hl">ipsum</strong> vel elit ultrices viverra.</p>
  </div>
</section>

<section class="band abs">
  <div class="panel abs">
    <div class="panel-divider abs"></div>
    <article class="about abs">
      <h2 class="section-title">Only One Reputation</h2>
      <p>We understand that you only have one reputation and provide services to both monitor how you are perceived online and reputation management services to allow you to ensure that you are in control of how your business is perceived online.</p>
      <p>Reputation Management is not simply for those who have suffered negative perception previously, but for all businesses to ensure that the most valuable asset they have is protected: their Reputation.</p>
      <p>Brightmeadow is a web-based service which provides real-time data to businesses on how their brand, intellectual copyright and overall reputation are portrayed on the internet. By scanning the internet for target words or phrases, the name of business, product brands and the name of key individual a report based on the positive or negative nature of how the business is perceived is returned</p>
      <a class="btn">Read More</a>
    </article>
    <aside class="news abs">
      <h2 class="section-title">Latest News</h2>
      <div class="news-item">
        <div class="news-thumb" role="img" aria-label="News photo of a group at an event"></div>
        <span class="news-date">21-03-2012</span>
        Lorem Ipsum is simply dummy text of the printing and typesetting industry. Lorem Ipsum has been the industry's standard dummy text ever since the 1500s,
      </div>
      <div class="news-item">
        <div class="news-thumb" role="img" aria-label="News photo of a business team"></div>
        <span class="news-date">20 03-2012</span>
        Lorem Ipsum is simply dummy text of the printing and typesetting industry. Lorem Ipsum has been the industry's standard dummy text ever since the 1500s,
      </div>
      <a class="btn">Read More</a>
    </aside>
  </div>
</section>

<section class="press abs" aria-label="As featured in">
  <div class="press-list abs">
    <span class="press-name">Morning Ledger</span>
    <span class="press-name boxed"><i></i>NVR</span>
    <span class="press-name">The Wayfarer</span>
    <span class="press-name">The Sunday Courier</span>
  </div>
</section>

<footer class="site-footer abs">
  <ul class="footer-col abs" style="left:100px">
    <li>Reputation Management</li>
    <li>Online Reputation Management – ORM</li>
    <li>Brand Protection</li>
    <li>Internet Online Defamation</li>
    <li>Online Reputation</li>
  </ul>
  <ul class="footer-col abs" style="left:321px">
    <li>Pro-Active Reputation Management</li>
    <li>About Brightmeadow</li>
    <li>Authors</li>
    <li>Contact</li>
    <li>Reputation Monitoring</li>
  </ul>
  <ul class="footer-col abs" style="left:527px;top:25px">
    <li>Reputation Correction</li>
    <li>Prices</li>
    <li>Privacy Policy</li>
    <li>Terms and Conditions of use</li>
  </ul>
  <div class="footer-rule abs"></div>
  <p class="copyright abs">© Copyright Brightmeadow. All Rights Reserved All Rights Reserved | Vat 000123456 | 4th Floor Linden House | Orchard Row | Harrowfield | HF1 2AB</p>
  <div class="social abs"><span></span><span></span><span></span><span></span><span></span><span></span></div>
  <div class="seal abs" role="img" aria-label="Gold satisfaction guarantee seal with red ribbon"></div>
</footer>

</body>
</html>
```